Heron Property Inspection business card

I am the principal inspector of Heron Property Inspections. I serve Northern Virginia from Winchester to Arlington.Associate, Federated Guild of Dwelling Examiners (FGDE)Graduate, FGDE Home Inspectors CourseNational Association of Home Inspectors ExamI'd like the business card to look more professional than comical.I pulled the attached picture off the web. I'd like to have something like that or an image of a house as my logo on the cards.

Target Market(s)

Persons who recently purchased a home.

Industry/Entity Type

Business

Contact Information for Business Card

Bob AllenBadger Home Inspections, LLC.4455 River RoadBluemont, Virginia 20135cell: 703-231-6680e-mail: tkmarlow@postvale.net

Font styles to use
Serif
Sans Serif

Requirements
Must have
• I'd like to have a logo, something that identifies me as a home inspector. The attached images are something that I'd like to have incorporated into my business card logo.
Nice to have
• I'd like a sketch of a house and/or a magnifying glass showing a house being inspected. The attached images are used as a suggestion only, I do not own the images.
Should not have
• Gimmicky stuff. I want to appear professional and trustworthy.

```html
<!DOCTYPE html>
<html lang="en">
<head>
<meta charset="utf-8">
<title>Heron Property Inspections – Business Card</title>
<link rel="stylesheet" href="https://fonts.googleapis.com/css2?family=Tenor+Sans&display=swap">
<style>
  :root {
    --backdrop: #e4e2df;
    --card: #f7f7f6;
    --ink: #3a3a3c;
    --accent: #b3262b;
    --band-dark: #8a1518;
    --band-light: #c4353a;
    --rule: #2e2e30;
    --on-band: #ffffff;
  }
  * { margin: 0; padding: 0; box-sizing: border-box; }
  html, body {
    width: 1200px; height: 818px; overflow: hidden;
    background: var(--backdrop);
    font-family: "Tenor Sans", sans-serif;
  }
  .card {
    position: absolute; left: 75px; top: 109px;
    width: 1050px; height: 600px;
    background: var(--card);
    box-shadow: 0 10px 30px rgba(0,0,0,.18);
    overflow: hidden;
  }
  .brand {
    position: absolute; left: 70px; top: 158px;
    display: flex; align-items: flex-start; gap: 22px;
  }
  .brand-mark {
    flex: none; width: 44px; height: 44px; margin-top: 12px;
    background: var(--accent);
  }
  .wordmark {
    color: var(--ink);
    line-height: 1.12;
  }
  .wordmark .owner { font-size: 48px; }
  .wordmark .company { font-size: 38px; }
  .person {
    position: absolute; right: 90px; top: 62px; text-align: right;
  }
  .person .name { font-size: 40px; color: var(--ink); }
  .person .role { font-size: 22px; color: var(--accent); margin-top: 4px; letter-spacing: .5px; }
  .rule {
    position: absolute; left: 0; width: 100%; height: 3px; background: var(--rule);
  }
  .rule.top { top: 296px; }
  .rule.bottom { top: 521px; }
  .band {
    position: absolute; left: 0; top: 306px; width: 100%; height: 208px;
    background: linear-gradient(100deg, var(--band-dark) 0%, var(--band-light) 45%, var(--band-dark) 100%);
    color: var(--on-band);
  }
  .contact-line {
    position: absolute; display: flex; align-items: center; gap: 16px;
    font-size: 27px; letter-spacing: .3px;
  }
  .contact-line svg { flex: none; }
  .phone { left: 70px; top: 108px; }
  .email { left: 70px; top: 152px; }
  .address { right: 90px; top: 26px; align-items: flex-start; }
  .address .lines { line-height: 1.3; }
</style>
</head>
<body>
  <div class="card">
    <div class="brand">
      <div class="brand-mark"></div>
      <div class="wordmark">
        <div class="owner">Tim Marlow</div>
        <div class="company">Heron Property Inspections, LLC</div>
      </div>
    </div>

    <div class="person">
      <div class="name">Employee Name</div>
      <div class="role">Managing Director</div>
    </div>

    <div class="rule top"></div>
    <div class="band">
      <div class="contact-line address">
        <svg width="30" height="30" viewBox="0 0 30 30" aria-hidden="true">
          <rect width="30" height="30" rx="3" fill="#fff"/>
          <path d="M15 5a7 7 0 0 0-7 7c0 5 7 13 7 13s7-8 7-13a7 7 0 0 0-7-7z" fill="#b3262b"/>
          <circle cx="15" cy="12" r="2.8" fill="#fff"/>
        </svg>
        <div class="lines">7182 Quarry Lane Fernhill<br>Virginia 20148</div>
      </div>
      <div class="contact-line phone">
        <svg width="30" height="30" viewBox="0 0 30 30" aria-hidden="true">
          <rect width="30" height="30" rx="3" fill="#fff"/>
          <rect x="9" y="5" width="12" height="20" rx="2" fill="none" stroke="#b3262b" stroke-width="2"/>
          <rect x="12" y="8" width="6" height="9" fill="#b3262b"/>
          <circle cx="15" cy="21" r="1.4" fill="#b3262b"/>
        </svg>
        <span>703-555-0192</span>
      </div>
      <div class="contact-line email">
        <svg width="30" height="30" viewBox="0 0 30 30" aria-hidden="true">
          <rect width="30" height="30" rx="3" fill="#fff"/>
          <rect x="6" y="9" width="18" height="13" fill="none" stroke="#b3262b" stroke-width="2"/>
          <path d="M6 9l9 7 9-7" fill="none" stroke="#b3262b" stroke-width="2"/>
        </svg>
        <span>tkmarlow@postvale.net</span>
      </div>
    </div>
    <div class="rule bottom"></div>
  </div>
</body>
</html>
```